Brookvane Billboard

Please design a billboard using my photos and logos.
For photo of truck please crop the truck itself out and not have the trees / dirt in photo.
Please put " Best Prices in Sevier County"
Please put " 30-yard Dumpsters Starting at 600.00"
Please put " 16-yard Dumpsters Starting at 300.0"
Please put " Delivery and Pickup 7 Days a week"
Billboard size will be 10 ft tall 30 ft wide

```html
<!DOCTYPE html>
<html lang="en">
<head>
<meta charset="utf-8">
<title>Brookvane Dumpsters Billboard</title>
<link rel="stylesheet" href="https://fonts.googleapis.com/css2?family=Nunito:wght@800;900&display=swap">
<style>
  :root {
    --page: #e9e9ec;
    --board-black: #000000;
    --band-purple: #2a1947;
    --accent-purple: #8a45cf;
    --tick-purple: #9b5bdb;
    --white: #ffffff;
    --truck-white: #e6e6e8;
    --truck-purple: #4b2a7f;
  }
  * { margin: 0; padding: 0; box-sizing: border-box; }
  html, body {
    width: 1200px;
    height: 879px;
    overflow: hidden;
    background: var(--page);
  }
  .canvas {
    position: relative;
    width: 1200px;
    height: 879px;
  }
  .billboard {
    position: absolute;
    left: 0;
    top: 240px;
    width: 1200px;
    height: 400px;
    background: var(--board-black);
    overflow: hidden;
    font-family: "Nunito", "Verdana", sans-serif;
  }
  .billboard__band {
    position: absolute;
    inset: 0;
    width: 1200px;
    height: 400px;
  }
  .brand {
    position: absolute;
    left: 42px;
    top: 26px;
    color: var(--white);
    font-weight: 900;
    text-transform: uppercase;
    line-height: 1;
  }
  .brand__name {
    display: block;
    font-size: 82px;
    letter-spacing: 1px;
  }
  .brand__sub {
    display: block;
    font-size: 46px;
    letter-spacing: 1px;
    margin-left: 150px;
    margin-top: 2px;
  }
  .offers {
    position: absolute;
    left: 22px;
    top: 190px;
    list-style: none;
  }
  .offers__item {
    display: flex;
    align-items: center;
    gap: 12px;
    color: var(--white);
    font-weight: 800;
    font-size: 24px;
    line-height: 34px;
    letter-spacing: 0.3px;
  }
  .offers__tick {
    width: 20px;
    height: 20px;
    flex: none;
  }
  .offers__price { color: var(--accent-purple); }
  .truck {
    position: absolute;
    left: 622px;
    top: 52px;
    width: 540px;
    height: 322px;
    border-radius: 18px 18px 40px 40px;
    background: linear-gradient(90deg, var(--truck-white) 0%, var(--truck-white) 48%, var(--truck-purple) 58%, var(--truck-purple) 100%);
  }
</style>
</head>
<body>
<main class="canvas">
  <section class="billboard">
    <svg class="billboard__band" viewBox="0 0 1200 400" aria-hidden="true">
      <path d="M0,336 C380,342 800,300 1200,200 L1200,400 L0,400 Z" fill="var(--white)"/>
      <path d="M0,344 C380,350 800,310 1200,212 L1200,400 L0,400 Z" fill="var(--band-purple)"/>
    </svg>

    <h1 class="brand">
      <span class="brand__name">Brookvane</span>
      <span class="brand__sub">Dumpsters</span>
    </h1>

    <ul class="offers">
      <li class="offers__item">
        <svg class="offers__tick" viewBox="0 0 20 20"><rect x="1" y="1" width="18" height="18" fill="none" stroke="var(--tick-purple)" stroke-width="2"/><path d="M5 10 L9 14 L16 5" fill="none" stroke="var(--tick-purple)" stroke-width="2.4"/></svg>
        Best Prices in Sevier County
      </li>
      <li class="offers__item">
        <svg class="offers__tick" viewBox="0 0 20 20"><rect x="1" y="1" width="18" height="18" fill="none" stroke="var(--tick-purple)" stroke-width="2"/><path d="M5 10 L9 14 L16 5" fill="none" stroke="var(--tick-purple)" stroke-width="2.4"/></svg>
        <span>30-yard Dumpsters Starting at <span class="offers__price">600.00</span></span>
      </li>
      <li class="offers__item">
        <svg class="offers__tick" viewBox="0 0 20 20"><rect x="1" y="1" width="18" height="18" fill="none" stroke="var(--tick-purple)" stroke-width="2"/><path d="M5 10 L9 14 L16 5" fill="none" stroke="var(--tick-purple)" stroke-width="2.4"/></svg>
        <span>16-yard Dumpsters Starting at <span class="offers__price">300.0</span></span>
      </li>
      <li class="offers__item">
        <svg class="offers__tick" viewBox="0 0 20 20"><rect x="1" y="1" width="18" height="18" fill="none" stroke="var(--tick-purple)" stroke-width="2"/><path d="M5 10 L9 14 L16 5" fill="none" stroke="var(--tick-purple)" stroke-width="2.4"/></svg>
        Delivery and Pickup 7 Days a week
      </li>
    </ul>

    <div class="truck" role="img" aria-label="Photo of a white roll-off truck carrying a purple dumpster"></div>
  </section>
</main>
</body>
</html>
```